Redesign of business card for Cedar Ridge Mechanical

We are looking for a new design for our business cards for Cedar Ridge Mechanical. We are a plumbing & HVAC construction company, operating on the West Coast of Canada and USA. Logo attached.
Industry/Entity Type
Construction - Plumbing & HVAC
Contact Information for Business Card
Name, address, phone numbers, email, website address
Look and feel
Each slider illustrates characteristics of the customer's brand and the style your logo design should communicate.

```html
<!DOCTYPE html>
<html lang="en">
<head>
<meta charset="utf-8">
<title>Cedar Ridge Mechanical – Business Card</title>
<link rel="stylesheet" href="https://fonts.googleapis.com/css2?family=Lato:wght@400;700;900&display=swap">
<style>
  :root {
    --ink: #0b0b0b;
    --paper: #ffffff;
    --swoosh: #9a9a9a;
    --stage: #d9d9d9;
    --muted: #2a2a2a;
  }
  * { box-sizing: border-box; margin: 0; padding: 0; }
  html, body { width: 1200px; height: 913px; overflow: hidden; }
  body {
    background: var(--stage);
    font-family: "Lato", sans-serif;
    position: relative;
  }
  .card {
    position: absolute;
    left: 250px;
    width: 700px;
    height: 400px;
    border-radius: 26px;
    overflow: hidden;
  }
  .card--front { top: 24px; background: var(--ink); }
  .card--back { top: 489px; background: var(--paper); }

  .brand {
    display: flex;
    align-items: center;
    gap: 18px;
    font-weight: 900;
    text-transform: uppercase;
    letter-spacing: 2px;
  }
  .brand__mark { flex: none; }
  .card--front .brand {
    position: absolute;
    inset: 0;
    justify-content: center;
    color: var(--paper);
    font-size: 34px;
  }
  .card--front .brand__mark { width: 40px; height: 40px; background: var(--paper); }

  .card__bg { position: absolute; inset: 0; }

  .card--back .brand {
    position: absolute;
    left: 44px; top: 110px;
    color: var(--ink);
    font-size: 24px;
  }
  .card--back .brand__mark { width: 30px; height: 30px; background: var(--ink); }

  .person {
    position: absolute;
    right: 30px; top: 52px;
    text-align: right;
    padding-right: 14px;
    border-right: 8px solid var(--ink);
  }
  .person__name { font-size: 24px; font-weight: 700; color: var(--ink); letter-spacing: 0.5px; }
  .person__role { font-size: 15px; color: var(--muted); margin-top: 2px; }

  .contacts {
    position: absolute;
    left: 40px; bottom: 22px;
    list-style: none;
    color: var(--paper);
    font-size: 18px;
  }
  .contacts li { display: flex; align-items: center; gap: 10px; line-height: 27px; }
  .contacts svg { width: 16px; height: 16px; fill: var(--paper); flex: none; }

  .address {
    position: absolute;
    right: 32px; bottom: 90px;
    color: var(--paper);
    font-size: 17px;
    line-height: 25px;
    text-align: right;
  }
</style>
</head>
<body>
  <section class="card card--front">
    <div class="brand"><span class="brand__mark"></span>Cedar Ridge Mechanical</div>
  </section>

  <section class="card card--back">
    <svg class="card__bg" viewBox="0 0 700 400" preserveAspectRatio="none" aria-hidden="true">
      <path d="M0 236 C 230 232, 470 200, 700 110 L700 146 C 470 228, 230 250, 0 250 Z" fill="var(--swoosh)"/>
      <path d="M0 258 C 230 256, 470 236, 700 156 L700 400 L0 400 Z" fill="var(--ink)"/>
    </svg>

    <div class="brand"><span class="brand__mark"></span>Cedar Ridge Mechanical</div>

    <div class="person">
      <div class="person__name">DANIEL HARPER</div>
      <div class="person__role">Managing Director</div>
    </div>

    <ul class="contacts">
      <li><svg viewBox="0 0 16 16"><path d="M3 1h3l1.5 4-2 1.3a9 9 0 0 0 4.2 4.2L11 8.5l4 1.5v3a2 2 0 0 1-2 2A13 13 0 0 1 1 3a2 2 0 0 1 2-2z"/></svg>123 456 789</li>
      <li><svg viewBox="0 0 16 16"><path d="M4 0h8a1 1 0 0 1 1 1v14a1 1 0 0 1-1 1H4a1 1 0 0 1-1-1V1a1 1 0 0 1 1-1zm1 2v10h6V2zm3 11a1 1 0 1 0 0 2 1 1 0 0 0 0-2z"/></svg>123 456 789</li>
      <li><svg viewBox="0 0 16 16"><path d="M1 3h14v10H1zm1.5 1.5v.3L8 9l5.5-4.2v-.3zm0 2.2v4.8h11V6.7L8 11z"/></svg>info@yourgmail.com</li>
      <li><svg viewBox="0 0 16 16"><path d="M8 0a8 8 0 1 0 0 16A8 8 0 0 0 8 0zm0 2a6 6 0 0 1 5.7 4H10L8 4 6 6H2.3A6 6 0 0 1 8 2zm-5.7 6h3.2l2 3-1 3A6 6 0 0 1 2.3 8zm7 5.8 1.2-3.8 3-2A6 6 0 0 1 9.3 13.8z"/></svg>www.yourwebsite.com</li>
    </ul>

    <div class="address">Your address, City<br>State, Zip 1234</div>
  </section>
</body>
</html>
```